Garlic Farm for Farm Sales/Restaurant sales

Need a professional, but appealing to agriculture world. We are selling 27 kinds of Organic Garlic from a farm in Simla,CO. I have uploaded logo and business information-we are going to need a template, because I will need to use it for four separate people.
-We are trying to appeal to Farm to table restaurants
-As well as growers/farmers

Target Market(s)

Agriculture Sales/Restaurants-Organic

Industry/Entity Type

Agriculture

Contact Information for Business Card

Want it to look more unique then your average kelto stock card- I want it to look amazing

Font styles to use
Sans Serif

Colors
0455a3
ec1f27
fbed22
ffffff

Requirements
Must have
• Just be creative
Nice to have
• Colorful
Should not have
• plain

```html
<!DOCTYPE html>
<html lang="en">
<head>
<meta charset="utf-8">
<title>Sunreach Garlic — Business Card</title>
<link rel="stylesheet" href="https://fonts.googleapis.com/css2?family=Open+Sans:wght@400;600;700&display=swap">
<style>
  :root {
    --stage: #ece7e2;
    --card-dark: #2b2828;
    --card-light: #ffffff;
    --ink-light: #ffffff;
    --brand-navy: #1b3468;
    --brand-red: #d0222d;
    --brand-gold: #f7d31c;
  }
  * { margin: 0; padding: 0; box-sizing: border-box; }
  html, body { width: 1200px; height: 900px; overflow: hidden; }
  body {
    background: var(--stage);
    font-family: "Open Sans", sans-serif;
    position: relative;
  }
  .card {
    position: absolute;
    border-radius: 18px;
    box-shadow: 0 8px 22px rgba(0,0,0,0.22);
  }
  .card--back {
    left: 78px; top: 34px; width: 588px; height: 364px;
    background: var(--card-dark);
    color: var(--ink-light);
    text-align: center;
  }
  .holder-name {
    position: absolute; left: 0; right: 0; top: 72px;
    font-size: 18px; font-weight: 700; line-height: 24px;
  }
  .holder-name span {
    display: inline-block;
    padding: 0 2px 1px;
    border-bottom: 1.5px solid var(--ink-light);
  }
  .holder-role {
    position: absolute; left: 0; right: 0; top: 101px;
    font-size: 15px; line-height: 20px;
  }
  .contact-list {
    position: absolute; left: 0; right: 0; top: 166px;
    list-style: none;
    font-size: 15px; line-height: 20px;
  }
  .contact-address {
    position: absolute; left: 0; right: 0; top: 254px;
    font-size: 15px; line-height: 20px;
  }
  .card--front {
    left: 390px; top: 506px; width: 564px; height: 349px;
    background: var(--card-light);
  }
  .brand {
    position: absolute; left: 0; right: 0; top: 140px;
    display: flex; align-items: center; justify-content: center; gap: 16px;
  }
  .brand-mark {
    width: 62px; height: 62px; border-radius: 50%;
    background: var(--brand-red);
    flex: none;
  }
  .brand-name {
    font-size: 38px; font-weight: 700; line-height: 1;
    color: var(--brand-navy);
  }
</style>
</head>
<body>
  <section class="card card--back">
    <h1 class="holder-name"><span>DANIEL AVERY</span></h1>
    <p class="holder-role">Managing Director</p>
    <ul class="contact-list">
      <li>044-555-0132</li>
      <li>123-555-0147</li>
      <li>hello@sunreachgarlic.com</li>
      <li>www.sunreachgarlic.com</li>
    </ul>
    <p class="contact-address">4870 Prairie Road | Simla, CO | 80835</p>
  </section>

  <section class="card card--front">
    <div class="brand">
      <span class="brand-mark"></span>
      <span class="brand-name">Sunreach Garlic</span>
    </div>
  </section>
</body>
</html>
```